Brell Stone Company Business Cards

Front and Back Business Card - logo and text setup - cool design. I need workable photoshop or illustrator files so I can setup each employee card with design that is created
Updates

Hi everyone, thank you for the great entries. Please no more white and blue cards - there are so many already - black and silver only now please. thanks!

Target Market(s)

Construction Industry - Facility Managers

Industry/Entity Type

Construction

Contact Information for Business Card

I really like contemporary simplistic looks - clean neat....not opposed to seeing some black backrounds

Requirements
Must have
• Logo/website address with design on front only - www.brellstone-example.com (logo attached)
• Back:
• Name/Title/Company Address/Phone/email address
Nice to have
• Cool design
Should not have
• Nothing gimmicky like Fire or Water - since we are a Fire Protection company - it has all been done

```html
<!DOCTYPE html>
<html lang="en">
<head>
<meta charset="utf-8">
<title>Brell Stone Company Business Cards</title>
<link rel="stylesheet" href="https://fonts.googleapis.com/css2?family=Source+Sans+3:ital,wght@0,400;0,700;0,900;1,700&display=swap">
<style>
  :root {
    --stage: #c9cdd1;
    --red: #ff2222;
    --blue: #0424a0;
    --black: #000000;
    --white: #ffffff;
    --text-font: "Source Sans 3", Arial, sans-serif;
  }
  html, body {
    margin: 0;
    padding: 0;
    width: 1200px;
    height: 1193px;
    overflow: hidden;
    background: var(--stage);
  }
  .canvas {
    position: relative;
    width: 1200px;
    height: 1193px;
  }
  .card {
    position: absolute;
    width: 872px;
    height: 499px;
    display: block;
    font-family: var(--text-font);
  }
  .card--details { left: 261px; top: 66px; }
  .card--brand { left: 61px; top: 623px; }
  .brand-name { font-weight: 900; }
  .person-name, .person-title { font-weight: 700; font-style: italic; }
  .address, .contact { font-weight: 400; }
</style>
</head>
<body>
<main class="canvas">

  <svg class="card card--details" viewBox="0 0 1050 600" role="group" aria-label="Business card with name and contact details">
    <defs>
      <linearGradient id="details-wash" x1="0" y1="0" x2="1050" y2="600" gradientUnits="userSpaceOnUse">
        <stop offset="0" stop-color="#000000"/>
        <stop offset="0.3" stop-color="#0a0a2a"/>
        <stop offset="0.55" stop-color="#0424a0"/>
        <stop offset="0.85" stop-color="#d81e3a"/>
        <stop offset="1" stop-color="#ff2222"/>
      </linearGradient>
    </defs>
    <rect class="decor-area" width="1050" height="600" rx="20" fill="url(#details-wash)" role="img" aria-label="Decorative sweeping bands in red, black and blue"/>

    <text class="brand-name" x="980" y="165" text-anchor="end" font-size="64" fill="var(--white)">Brell Stone Company</text>

    <text class="person-name" x="50" y="355" font-size="38" fill="var(--white)">Dana Morrow</text>
    <text class="person-title" x="50" y="402" font-size="34" fill="var(--white)">President</text>

    <text class="address" x="50" y="468" font-size="28" fill="var(--white)">48 Harbor Lane</text>
    <text class="address" x="50" y="505" font-size="28" fill="var(--white)">Westfield, NY 10000</text>

    <text class="contact" x="963" y="463" text-anchor="end" font-size="27" fill="var(--white)">(555) 010-4827</text>
    <text class="contact" x="963" y="510" text-anchor="end" font-size="27" fill="var(--white)">info@brellstone-example.com</text>
    <text class="contact" x="963" y="556" text-anchor="end" font-size="27" fill="var(--white)">www.brellstone-example.com</text>

    <g class="icon icon-phone" transform="translate(983,442)" fill="var(--white)">
      <path d="M4,1 L9,1 L11,7 L8,9 C9.5,13 12,16 16,18 L18,15 L24,17 L24,22 C24,24 22,25 20,25 C10,24 1,15 0,5 C0,3 2,1 4,1 Z"/>
    </g>
    <g class="icon icon-mail" transform="translate(983,492)">
      <rect x="0" y="0" width="27" height="19" fill="var(--white)"/>
      <path d="M1,1 L13.5,11 L26,1" fill="none" stroke="#c81e40" stroke-width="2.5"/>
      <path d="M1,18 L10,9 M26,18 L17,9" fill="none" stroke="#c81e40" stroke-width="2"/>
    </g>
    <g class="icon icon-globe" transform="translate(996,546)" fill="none" stroke="var(--white)" stroke-width="2">
      <circle r="13"/>
      <ellipse rx="6" ry="13"/>
      <line x1="-13" y1="0" x2="13" y2="0"/>
      <path d="M-11,-6 H11 M-11,6 H11"/>
      <line x1="0" y1="-13" x2="0" y2="13"/>
    </g>
  </svg>

  <svg class="card card--brand" viewBox="0 0 1050 600" role="group" aria-label="Business card with company name and website">
    <rect class="bg" width="1050" height="600" rx="20" fill="var(--red)"/>
    <text class="brand-name" x="525" y="300" text-anchor="middle" font-size="86" fill="var(--white)">Brell Stone Company</text>
    <text class="contact website" x="525" y="426" text-anchor="middle" font-size="32" letter-spacing="6" fill="var(--white)">www.brellstone-example.com</text>
  </svg>

</main>
</body>
</html>
```